Varlomatch E-commerce Website Design

I'm looking into having my e-comm website built. We are an investment company that is investing in a private label focused on a rising sport category called Pickleball in EU market.

We will provide top quality material and acessories for players be ready to go to courts. We will have a range of: Rackets, Set of balls, Net, Lines, overgrip, water bottle, player bag.

As it´s a new sports category we would like to see an architecture that alows us to share some storytelling about the category, the brand and lead to purchase of our products.

We will position our self as an inclusive and fun brand that you can reach out to find more info about Pickleball Sport, buy your pickleball stuff and have fun. Its all about action and fun.

Target Market(s)

Europe Market

Industry/Entity Type

Pickleball (Sports)

Coding

Coded - Design and coding required

Number of Pages Required

1 page

Requirements
Must have
• E-commerce look and feel
Nice to have
• A bit of storytelling about the brand and specially the category (Pickleball).

```html
<!DOCTYPE html>
<html lang="en">
<head>
<meta charset="utf-8">
<title>Varlomatch – Pickleball Gear</title>
<link href="https://fonts.googleapis.com/css2?family=Tinos:wght@700&family=Lato:wght@400;700&family=Roboto:wght@500;700&display=swap" rel="stylesheet">
<style>
:root{
  --teal:#3aaaa5;
  --ink:#111;
  --text:#555;
  --grey:#f3f3f3;
  --white:#fff;
}
*{box-sizing:border-box;margin:0;padding:0}
html,body{width:1200px;height:3787px;overflow:hidden}
body{position:relative;font-family:"Lato",sans-serif;color:var(--ink);background:var(--white)}
.abs{position:absolute}
.promo-bar{top:0;left:0;width:1200px;height:51px;background:#000;color:#fff;font-size:14px;display:flex;align-items:center;justify-content:center}
.header{top:51px;left:0;width:1200px;height:102px}
.logo{font-family:"Roboto",sans-serif;font-weight:700;font-size:25px;letter-spacing:1px;text-transform:uppercase}
.header .logo{left:110px;top:35px}
.nav{left:420px;top:41px;display:flex;gap:25px;font-size:14px;color:#333}
.nav .active{color:var(--teal);border-bottom:2px solid var(--teal);padding-bottom:4px}
.cart-btn{left:904px;top:30px;width:42px;height:42px;background:var(--teal);display:flex;align-items:center;justify-content:center}
.search-btn{left:955px;top:30px;width:42px;height:42px;border:2px solid #000;display:flex;align-items:center;justify-content:center}
.login{left:1028px;top:41px;font-size:14px;color:#333;display:flex;gap:6px;align-items:center}
.photo{overflow:hidden}
.hero{top:153px;left:0;width:1200px;height:598px;
  background:
    radial-gradient(ellipse 260px 420px at 360px 300px,rgba(190,60,70,.45),transparent 70%),
    radial-gradient(ellipse 180px 380px at 70px 380px,rgba(60,60,75,.6),transparent 70%),
    linear-gradient(180deg,#3b4a44 0%,#3f6d58 30%,#4f8a6c 55%,#5c7f8a 80%,#7c8c92 100%)}
.hero-box{left:519px;top:247px;width:594px;height:174px;background:rgba(50,50,50,.72);text-align:center}
.hero-box h1{font-family:"Tinos",serif;font-size:76px;color:#fff;line-height:1;margin-top:16px;letter-spacing:1px;white-space:nowrap}
.btn-teal{background:var(--teal);color:#fff;font-family:"Tinos",serif;font-weight:700;font-size:15px;display:inline-flex;align-items:center;justify-content:center}
.hero-box .btn-teal{width:128px;height:44px;margin-top:18px}
.dots{left:561px;top:529px;display:flex;gap:8px}
.dots span{width:13px;height:13px;border-radius:50%;border:2px solid #fff}
.dots span:first-child{background:#fff}
.section-title{width:1200px;left:0;text-align:center;font-family:"Tinos",serif;font-weight:700;font-size:44px;letter-spacing:.5px}
.about-text{left:190px;top:895px;width:820px;text-align:center;font-size:14px;line-height:26px;color:var(--text)}
.cat-card{top:1000px;width:313px;height:376px}
.cat-card .btn-teal{position:absolute;left:78px;top:170px;width:158px;height:40px;letter-spacing:.5px}
.arrow{width:24px;height:24px}
.products{top:1478px;left:0;width:1200px;height:531px;background:var(--grey)}
.prod-card{top:1621px;width:234px;height:298px;background:#fff}
.prod-card .thumb{position:absolute;left:22px;top:18px;width:190px;height:180px}
.prod-card .name{position:absolute;left:18px;top:218px;font-size:21px;color:#222;white-space:nowrap}
.prod-card .price{position:absolute;left:18px;top:250px;font-size:21px;color:var(--teal)}
.badge{left:605px;top:1621px;width:126px;height:32px;background:var(--teal);color:#fff;font-size:14px;font-weight:700;display:flex;align-items:center;justify-content:center}
.quote-box{left:506px;top:2225px;width:582px;height:294px;background:var(--grey)}
.quote-box p{position:absolute;left:30px;top:97px;width:520px;font-size:14px;line-height:21.5px;color:var(--text)}
.quote-box .author{position:absolute;left:30px;top:228px;font-size:14px;font-weight:700;color:#222}
.follow-img{top:2750px;height:331px}
.newsletter{top:3113px;left:0;width:1200px;height:346px;
  background:
    radial-gradient(ellipse 200px 260px at 270px 150px,rgba(30,90,90,.35),transparent 70%),
    radial-gradient(ellipse 200px 260px at 960px 160px,rgba(30,90,90,.3),transparent 70%),
    linear-gradient(180deg,#3aaaa5,#36a09b)}
.newsletter h2{position:absolute;top:85px;left:0;width:1200px;text-align:center;font-family:"Tinos",serif;font-weight:700;font-size:40px;color:#fff}
.email{position:absolute;left:350px;top:143px;width:500px;height:46px;border:2px solid #fff;color:#fff;font-size:14px;display:flex;align-items:center;padding-left:22px;gap:6px}
.subscribe{position:absolute;left:525px;top:212px;width:150px;height:44px;background:#fff;color:#222;font-family:"Roboto",sans-serif;font-weight:700;font-size:13px;display:flex;align-items:center;justify-content:center}
.footer .logo{left:110px;top:3540px}
.f-col{top:3540px;display:flex;flex-direction:column;gap:12px;font-size:13px;color:#333;line-height:18px}
.f-col.social span{display:flex;align-items:center;gap:14px}
.f-col.social i{width:10px;height:10px;background:#222;display:inline-block}
.copyright{top:3735px;left:0;width:1200px;text-align:center;font-size:13px;color:#333}
</style>
</head>
<body>
<div class="abs promo-bar">15% OFF YOUR FIRST ORDER</div>

<header class="abs header">
  <div class="abs logo">Varlomatch</div>
  <nav class="abs nav">
    <span class="active">HOME</span><span>SHOP</span><span>CAMPAIGN</span><span>ABOUT</span><span>CONTACT</span><span>SIZE GUIDE</span>
  </nav>
  <div class="abs cart-btn"><svg width="20" height="24" viewBox="0 0 20 24" fill="none" stroke="#fff" stroke-width="1.6"><rect x="2" y="7" width="16" height="15"/><path d="M6 7V5a4 4 0 0 1 8 0v2"/><text x="10" y="19" font-size="9" text-anchor="middle" fill="#fff" stroke="none" font-family="Lato">0</text></svg></div>
  <div class="abs search-btn"><svg width="14" height="14" viewBox="0 0 14 14" fill="none" stroke="#000" stroke-width="2"><circle cx="6" cy="6" r="4.5"/><path d="M9.5 9.5L13 13"/></svg></div>
  <div class="abs login"><svg width="11" height="12" viewBox="0 0 11 12" fill="#333"><circle cx="5.5" cy="3" r="3"/><path d="M0 12c0-4 2.5-5.5 5.5-5.5S11 8 11 12z"/></svg>LOGIN</div>
</header>

<section class="abs hero photo" role="img" aria-label="Two women playing pickleball on an outdoor court">
  <div class="abs hero-box">
    <h1>VARLOMATCH</h1>
    <span class="btn-teal">SHOP NOW</span>
  </div>
  <div class="abs dots"><span></span><span></span><span></span><span></span></div>
</section>

<h2 class="abs section-title" style="top:826px">ABOUT THE CATEGORY</h2>
<p class="abs about-text">Lorem ipsum dolor sit amet, consectetur adipiscing elit, sed do eiusmod tempor incididunt ut labore et dolore magna quis nostrud exercitation ullamco laboris nisi ut aliquip ex ea commodo consequat. Lorem ipsum dolor sit amet, consectetur adipiscing elit, sed do eiusmod tempor incididunt ut labore et dolore magna aliqua.</p>

<svg class="abs arrow" style="left:42px;top:1176px" viewBox="0 0 24 24" fill="none" stroke="#111" stroke-width="2.5"><path d="M15 3L7 12l8 9"/></svg>
<div class="abs cat-card" style="left:112px;background:radial-gradient(ellipse 120px 150px at 100px 130px,rgba(80,80,90,.55),transparent 75%),radial-gradient(ellipse 120px 150px at 215px 160px,rgba(110,130,110,.5),transparent 75%),linear-gradient(180deg,#2a62c8 0%,#2457bb 85%,#8aa3d8 88%,#2457bb 92%)" role="img" aria-label="Two pickleball rackets and a ball on a blue court"><span class="btn-teal">RACKETS</span></div>
<div class="abs cat-card" style="left:444px;background:radial-gradient(ellipse 150px 90px at 156px 225px,rgba(210,220,60,.8),transparent 75%),linear-gradient(180deg,#b9bfc2 0%,#8f9aa0 25%,#56698a 45%,#33466a 100%)" role="img" aria-label="Two yellow pickleballs on a court"><span class="btn-teal">SET OF BALLS</span></div>
<div class="abs cat-card" style="left:776px;background:radial-gradient(ellipse 130px 110px at 170px 170px,rgba(240,200,185,.85),transparent 75%),linear-gradient(180deg,#b8b07a 0%,#c9c2a0 40%,#d9a98e 70%,#c0704e 100%)" role="img" aria-label="Hands wrapping overgrip tape on a paddle handle"><span class="btn-teal">OVERGRIP</span></div>
<svg class="abs arrow" style="left:1132px;top:1176px" viewBox="0 0 24 24" fill="none" stroke="#111" stroke-width="2.5"><path d="M9 3l8 9-8 9"/></svg>

<section class="abs products"></section>
<h2 class="abs section-title" style="top:1552px">OUR PRODUCT</h2>
<svg class="abs arrow" style="left:42px;top:1744px" viewBox="0 0 24 24" fill="none" stroke="#111" stroke-width="2.5"><path d="M15 3L7 12l8 9"/></svg>
<div class="abs prod-card" style="left:112px"><div class="thumb" role="img" aria-label="Black sports armband pouch" style="background:radial-gradient(ellipse 62px 90px at 95px 90px,#1d1d1d 0%,#2a2a2a 55%,rgba(255,255,255,0) 100%)"></div><div class="name">Duis aute irure dolor</div><div class="price">$25.00</div></div>
<div class="abs prod-card" style="left:359px"><div class="thumb" role="img" aria-label="Yellow pickleball" style="background:radial-gradient(circle 78px at 95px 90px,#ead23a 0%,#dcbc2c 55%,rgba(255,255,255,0) 100%)"></div><div class="name">Duis aute irure dolor</div><div class="price">$25.00</div></div>
<div class="abs prod-card" style="left:606px"><div class="thumb" role="img" aria-label="White aluminium water bottle" style="background:radial-gradient(ellipse 40px 95px at 95px 95px,#e6e6e6 0%,#f2f2f2 55%,rgba(255,255,255,0) 100%)"></div><div class="name">Duis aute irure dolor</div><div class="price">$25.00</div></div>
<div class="abs badge">Best seller</div>
<div class="abs prod-card" style="left:853px"><div class="thumb" role="img" aria-label="Green and purple pickleball paddles" style="background:radial-gradient(ellipse 65px 90px at 95px 88px,#5a6f58 0%,#6a5280 55%,rgba(255,255,255,0) 100%)"></div><div class="name">Duis aute irure dolor</div><div class="price">$25.00</div></div>
<svg class="abs arrow" style="left:1132px;top:1744px" viewBox="0 0 24 24" fill="none" stroke="#111" stroke-width="2.5"><path d="M9 3l8 9-8 9"/></svg>

<h2 class="abs section-title" style="top:2087px">WHAT PEOPLE SAY</h2>
<div class="abs photo" style="left:112px;top:2162px;width:488px;height:418px;background:radial-gradient(ellipse 110px 200px at 250px 220px,rgba(170,210,60,.55),transparent 75%),radial-gradient(ellipse 90px 60px at 250px 290px,rgba(200,60,60,.45),transparent 75%),linear-gradient(180deg,#55606a 0%,#3e566c 35%,#2d4766 70%,#4b5a66 100%)" role="img" aria-label="Senior player crouched ready to return a shot"></div>
<div class="abs quote-box">
  <svg class="abs" style="left:30px;top:30px" width="62" height="46" viewBox="0 0 62 46" fill="#111"><circle cx="13" cy="32" r="12"/><path d="M2 30C2 14 10 4 24 2l1 5C14 10 10 18 10 30z"/><circle cx="46" cy="32" r="12"/><path d="M35 30C35 14 43 4 57 2l1 5C47 10 43 18 43 30z"/></svg>
  <p>"Lorem ipsum dolor sit amet, consectetur adipiscing elit, sed do eiusmod tempor incididunt ut labore et dolore magna aliqua. Ut enim ad minim veniam, quis nostrud exercitation ullamco laboris nisi ut aliquip ex ea commodo minim veniam, quis nostrud exercitation ullamco laboris nisi ut aliquip ex ea commodo consequat.t."</p>
  <div class="author">- John Doe</div>
</div>

<h2 class="abs section-title" style="top:2654px">FOLLOW US</h2>
<div class="abs follow-img" style="left:0;width:146px;background:radial-gradient(ellipse 70px 60px at 20px 200px,rgba(220,80,50,.8),transparent 75%),linear-gradient(160deg,#5c7448 0%,#4a5e3e 40%,#2c2f36 60%,#e6e6e6 62%,#2c2f36 70%)" role="img" aria-label="Paddle resting on a court line"></div>
<div class="abs follow-img" style="left:179px;width:403px;background:radial-gradient(ellipse 110px 100px at 200px 110px,rgba(150,100,100,.6),transparent 75%),linear-gradient(180deg,#7d878c 0%,#50585e 35%,#2f3236 60%,#3d3a3e 100%)" role="img" aria-label="Players tapping paddles over the net"></div>
<div class="abs follow-img" style="left:615px;width:403px;background:linear-gradient(180deg,#b9c4b6 0%,#7f9a6c 25%,#5d7584 45%,#4d6a92 60%,#8b4b45 85%,#a05a50 100%)" role="img" aria-label="Doubles match on an outdoor court"></div>
<div class="abs follow-img" style="left:1051px;width:149px;background:radial-gradient(ellipse 60px 80px at 110px 130px,rgba(220,180,160,.55),transparent 75%),linear-gradient(180deg,#7a7a7a 0%,#4f5666 50%,#354766 100%)" role="img" aria-label="Player holding a paddle and ball"></div>

<section class="abs newsletter" role="img" aria-label="Players on a court behind a teal tint">
  <h2>Subscribe Our Newsletter</h2>
  <div class="email"><svg width="13" height="10" viewBox="0 0 13 10"><rect width="13" height="10" fill="#fff"/><path d="M1 1.5l5.5 4 5.5-4" fill="none" stroke="#3aaaa5" stroke-width="1"/></svg>Email address</div>
  <div class="subscribe">SUBSCRIBE NOW</div>
</section>

<footer class="footer">
  <div class="abs logo">Varlomatch</div>
  <div class="abs f-col" style="left:443px"><span>Shop</span><span>Campaign</span><span>About Us</span><span>Contact Us</span><span>Size Guide</span></div>
  <div class="abs f-col" style="left:710px"><span>Privacy policy</span><span>Shipping &amp; Returns</span><span>Store Policy</span><span>Payment Methods</span><span>FAQ</span></div>
  <div class="abs f-col social" style="left:998px"><span><i></i>Kinpage</span><span><i></i>Chirper</span><span><i></i>Linkwork</span><span><i></i>Snapgram</span></div>
  <div class="abs copyright">© 2023 by Varlomatch. | All Rights Reserved</div>
</footer>
</body>
</html>
```